Stationery Design Project for Nimbora, Chicago

Nimbora, a street parking application which helps car drivers find a street parking spot by offering an ideal path along which to look for parking. This path is calculated by our algorithm based on data (e.g. historical data, baseball games schedule, etc.). Along this path the driver will find a spot and will also save 70% of the search time. Customer we target is reg. between 21 and 45 yo.

We envision something young, fresh, bright and original. Slightly abstract maybe. It should represent the idea and elements of finding street parking in the city, e.g. car(s), parking spot, people, city, etc. (just ideas!).

Logo is attached.

Requirement:
- Business Cards (2 Sided Full Color CMYK)
- Letterhead (1 Sided Full Color CMYK)
- Envelope (1 Sided Full Color CMYK)
- Sticker (1 Sided Full Color CMYK), round with a 2inch diameter.

Reason: We're starting to get more and more designs and need more time to look into all of them. Very exciting!! Thanks to everybody!

Hi all, we're in the process of selecting our favs. Though choices!!! Really good submissions. Will keep you posted and sorry for the delay.

Target Market(s)

Car drivers and owners between 21 and 45

Industry/Entity Type

Parking

Requirements
Must have
• Sticker should be round and include company URL nimbora.com and the new logo which we will attach soon.
Should not have
• Should not be too serious or boring.

```html
<!DOCTYPE html>
<html lang="en">
<head>
<meta charset="utf-8">
<title>Nimbora Business Card</title>
<link rel="stylesheet" href="https://fonts.googleapis.com/css2?family=Open+Sans:wght@400;600;700&display=swap">
<style>
  :root {
    --backdrop: #e6e7ea;
    --card-blue: #1c3394;
    --accent-cyan: #00aeef;
    --mark-blue: #1f8ad6;
    --band-dark: #0d0d0d;
    --band-mid: #5a5a5c;
    --ink-light: #ffffff;
  }
  * { box-sizing: border-box; margin: 0; padding: 0; }
  html, body {
    width: 954px;
    height: 1200px;
    overflow: hidden;
    background: var(--backdrop);
    font-family: "Open Sans", Arial, sans-serif;
    color: var(--ink-light);
  }
  .canvas { position: relative; width: 954px; height: 1200px; }

  .card {
    position: absolute;
    left: 103px;
    width: 795px;
    height: 455px;
    background: var(--card-blue);
    border-radius: 30px;
    overflow: hidden;
  }
  .card--front { top: 112px; }
  .card--back { top: 648px; }

  .top-tab {
    position: absolute;
    left: 284px;
    top: 0;
    width: 252px;
    height: 12px;
    background: var(--accent-cyan);
    border-radius: 0 0 8px 8px;
  }

  .brand-dot {
    position: absolute;
    left: 84px;
    width: 170px;
    height: 170px;
    border-radius: 50%;
    background: radial-gradient(circle at 50% 40%, #3fb4f0 0%, var(--mark-blue) 55%, #1456b0 100%);
  }
  .card--front .brand-dot { top: 75px; }
  .card--back .brand-dot { top: 82px; }

  .brand-name {
    position: absolute;
    left: 290px;
    font-size: 108px;
    font-weight: 600;
    letter-spacing: 1px;
    line-height: 1;
    color: var(--ink-light);
  }
  .card--front .brand-name { top: 100px; }
  .card--back .brand-name { top: 112px; }

  .holder { position: absolute; left: 49px; top: 300px; }
  .holder__name { font-size: 24px; font-weight: 700; line-height: 32px; }
  .holder__title { font-size: 18px; font-weight: 700; line-height: 26px; }

  .address {
    position: absolute;
    right: 29px;
    top: 306px;
    text-align: right;
    font-size: 19px;
    line-height: 28px;
  }

  .contact-band {
    position: absolute;
    left: 0;
    bottom: 0;
    width: 100%;
    height: 82px;
    background: linear-gradient(90deg, var(--band-dark) 0%, var(--band-mid) 50%, var(--band-dark) 100%);
    font-size: 19px;
    line-height: 27px;
  }
  .contact-band__phones { position: absolute; left: 49px; top: 12px; }
  .contact-band__web { position: absolute; right: 29px; top: 12px; text-align: right; }
  .label { font-weight: 700; }

  .back-contacts {
    position: absolute;
    left: 0;
    width: 100%;
    top: 381px;
    text-align: center;
    font-size: 19px;
    line-height: 28px;
  }
  .divider { margin: 0 10px; }
</style>
</head>
<body>
<main class="canvas">
  <section class="card card--front">
    <div class="top-tab"></div>
    <div class="brand-dot"></div>
    <div class="brand-name">nimbora</div>
    <div class="holder">
      <p class="holder__name">Your Name</p>
      <p class="holder__title">Designation</p>
    </div>
    <div class="address">
      <p>City Name, Street Name</p>
      <p>State Name, Country Code</p>
    </div>
    <div class="contact-band">
      <div class="contact-band__phones">
        <p><span class="label">t</span> : 123-456-7890</p>
        <p><span class="label">c</span> : 123-456-7890</p>
      </div>
      <div class="contact-band__web">
        <p><span class="label">e</span> : name@website.com</p>
        <p><span class="label">w</span> : www.website.com</p>
      </div>
    </div>
  </section>

  <section class="card card--back">
    <div class="brand-dot"></div>
    <div class="brand-name">nimbora</div>
    <p class="back-contacts">
      <span class="label">e</span> : name@website.com<span class="divider">|</span><span class="label">w</span> : www.website.com
    </p>
  </section>
</main>
</body>
</html>
```